Stylish Business Cards Wanted

- DOUBLE SIDED Design Required -

High end, edgy cards for a corporate and personal stylist. Must include logo,
Name: Belinda Harwick
Title: Director and Stylist
telephone : +61 8 7142 5809
email: belinda@theloombriefing.example
website: theloombriefing.example
Tag: Corporate Workwear & Uniform Specialist | Personal Stylist
Would like nice icons for telephone, email, website

Target Market(s)

Businesses wanting stylish uniforms, people wanting stylish wardrobes

Industry/Entity Type

Corporate Workwear Stylist

Contact Information for Business Card

I would like black, white and gold foiling incorporated in the design - possibly a touch of the other colours on my branding guide attached Name: Belinda Harwick Title: Director and Stylist telephone : +61 8 7142 5809 email: belinda@theloombriefing.example website: theloombriefing.example Tag: Corporate Workwear & Uniform Specialist | Personal Stylist Would like nice icons for telephone, email, website

Font styles to use
Other font styles liked:
• Raleway

Colors

Designer to choose colors to be used in the design.

Requirements
Must have
• Gold foil accents

```html
<!DOCTYPE html>
<html lang="en">
<head>
<meta charset="utf-8">
<title>The Loom Briefing — Business Cards</title>
<link rel="stylesheet" href="https://fonts.googleapis.com/css2?family=Lato:wght@400;700&display=swap">
<style>
  :root {
    --backdrop: #2a2522;
    --card-black: #161616;
    --gold: #e6bd55;
    --ink-light: #e4e6e4;
    --rule: #6b6b6b;
  }
  * { margin: 0; padding: 0; box-sizing: border-box; }
  html, body {
    width: 1200px;
    height: 842px;
    overflow: hidden;
    background: var(--backdrop);
    font-family: "Lato", "Helvetica Neue", Arial, sans-serif;
  }
  .sheet {
    position: relative;
    width: 1200px;
    height: 842px;
  }
  .card {
    position: absolute;
    top: 256px;
    width: 540px;
    height: 330px;
    background: var(--card-black);
    overflow: hidden;
  }
  .card--contact { left: 40px; }
  .card--brand { left: 620px; }

  /* Contact side */
  .band {
    position: absolute;
    left: 0;
    width: 100%;
    height: 13px;
    background: var(--gold);
  }
  .band--top { top: 0; }
  .band--bottom { bottom: 10px; }
  .contact {
    position: absolute;
    top: 92px;
    left: 0;
    width: 100%;
    text-align: center;
    color: var(--ink-light);
  }
  .contact__name {
    font-weight: 700;
    font-size: 24px;
    letter-spacing: 0.5px;
    text-transform: uppercase;
    color: var(--gold);
    line-height: 1;
  }
  .contact__title {
    margin-top: 4px;
    font-size: 15px;
    letter-spacing: 0.3px;
  }
  .contact__rule {
    width: 150px;
    height: 1px;
    margin: 14px auto 14px;
    background: var(--rule);
  }
  .contact__line {
    font-size: 15px;
    line-height: 21px;
    letter-spacing: 0.3px;
  }

  /* Brand side */
  .tab {
    position: absolute;
    width: 48px;
    height: 52px;
    background: var(--gold);
  }
  .tab--left { left: 0; top: 170px; }
  .tab--right { right: 0; top: 36px; }
  .brand {
    position: absolute;
    top: 110px;
    left: 0;
    width: 100%;
    display: flex;
    align-items: center;
    justify-content: center;
    gap: 12px;
  }
  .brand__mark {
    width: 12px;
    height: 12px;
    background: var(--gold);
  }
  .brand__name {
    font-weight: 700;
    font-size: 38px;
    letter-spacing: 1px;
    color: var(--ink-light);
  }
  .tagline {
    position: absolute;
    bottom: 40px;
    left: 0;
    width: 100%;
    text-align: center;
    font-size: 14px;
    letter-spacing: 0.3px;
    color: var(--ink-light);
  }
  .tagline__dot {
    display: inline-block;
    width: 6px;
    height: 6px;
    margin: 0 8px 2px;
    border-radius: 50%;
    background: var(--gold);
    vertical-align: middle;
  }
</style>
</head>
<body>
<main class="sheet">
  <section class="card card--contact" aria-label="Card back: contact details">
    <div class="band band--top"></div>
    <div class="contact">
      <p class="contact__name">Belinda Harwick</p>
      <p class="contact__title">Director and Stylist</p>
      <div class="contact__rule"></div>
      <p class="contact__line">+61 8 7142 5809</p>
      <p class="contact__line">belinda@theloombriefing.example</p>
      <p class="contact__line">theloombriefing.example</p>
    </div>
    <div class="band band--bottom"></div>
  </section>

  <section class="card card--brand" aria-label="Card front: brand">
    <div class="tab tab--right"></div>
    <div class="tab tab--left"></div>
    <div class="brand">
      <span class="brand__mark"></span>
      <span class="brand__name">The Loom Briefing</span>
    </div>
    <p class="tagline">Corporate Workwear &amp; Uniform Specialist<span class="tagline__dot"></span>Personal Stylist</p>
  </section>
</main>
</body>
</html>
```